Business card design Needed for new logo / Construction business, home extensions and new builds

We need a business card design using our new logo files which i will attach to this project :)

We are a small construction business specialising in home extensions, new builds and property development. We are very ambitious and would appreciate professional and elegant designs for our new business card.

Very serious about using the services on MakerQuarry and recently acquired our new logo from here :)

Please get involved, i will feedback when i can as i am very busy but can respond daily, thanks

Target Market(s)

People that want to build onto their houses, new building developments or adding too their existing property

Industry/Entity Type

Construction

Contact Information for Business Card

Renwick Tolliver Construction, Lionel Ashby (Managing Director), Tel 07822254961, email - info@renwick-tolliver, www.renwick-tolliver.co.uk

Colors

Designer to choose colors to be used in the design.

Requirements
Must have
• I like a deep grey on the back please. A lot of you have provided black from and back, try mixing things up a little. The black looks cool 😎 Thanks

```html
<!DOCTYPE html>
<html lang="en">
<head>
<meta charset="utf-8">
<title>Renwick Tolliver Construction – Business Card</title>
<link href="https://fonts.googleapis.com/css2?family=Arimo:wght@400;700&display=swap" rel="stylesheet">
<style>
  :root{
    --stage:#1e1e20;
    --gold-light:#f1cd6e;
    --gold:#d9a53a;
    --gold-deep:#b9801f;
    --ink:#141414;
    --charcoal:#3b3b3c;
    --charcoal-dark:#333334;
    --silver:#d9d9d9;
    --white:#f2f2f2;
    --accent-gold:#d69a2a;
  }
  *{margin:0;padding:0;box-sizing:border-box}
  html,body{width:1200px;height:779px;overflow:hidden}
  body{
    background:var(--stage);
    font-family:"Arimo",Arial,sans-serif;
    position:relative;
  }
  .card{
    position:absolute;
    width:560px;height:320px;
    border-radius:3px;
    box-shadow:0 10px 30px rgba(0,0,0,.45);
  }

  /* Front */
  .card-front{
    left:90px;top:70px;
    background:radial-gradient(ellipse at 55% 35%, var(--gold-light) 0%, var(--gold) 45%, var(--gold-deep) 100%);
    color:var(--ink);
    display:flex;flex-direction:column;align-items:center;justify-content:center;
  }
  .brand{
    display:flex;flex-direction:column;align-items:center;gap:12px;
  }
  .brand-mark{width:30px;height:30px;background:currentColor}
  .brand-name{
    font-weight:700;font-size:24px;letter-spacing:1.5px;text-transform:uppercase;
    text-align:center;line-height:1.2;
  }
  .front-web{
    margin-top:44px;font-size:14px;letter-spacing:4px;
  }

  /* Back */
  .card-back{
    left:550px;top:400px;
    background:linear-gradient(160deg, var(--charcoal) 0%, var(--charcoal-dark) 100%);
    border-bottom:2px solid var(--accent-gold);
    color:var(--white);
  }
  .card-back .brand{
    position:absolute;top:46px;left:0;right:0;color:var(--silver);gap:10px;
  }
  .card-back .brand-mark{width:24px;height:24px;background:var(--accent-gold)}
  .card-back .brand-name{font-size:20px;color:var(--silver)}
  .person{
    position:absolute;left:40px;top:210px;width:220px;text-align:right;
  }
  .person-name{color:var(--accent-gold);font-weight:700;font-size:26px}
  .person-role{font-size:16px;margin-top:4px}
  .divider{
    position:absolute;left:282px;top:180px;width:1px;height:96px;
    background:linear-gradient(to bottom, transparent, #9a9a9a 30%, #9a9a9a 70%, transparent);
  }
  .contacts{
    position:absolute;left:304px;top:190px;list-style:none;
    font-size:15px;
  }
  .contacts li{display:flex;align-items:center;gap:9px;margin-bottom:9px}
  .contacts svg{width:13px;height:13px;flex:none;fill:var(--accent-gold)}
</style>
</head>
<body>

<section class="card card-front" aria-label="Card front">
  <div class="brand">
    <span class="brand-mark"></span>
    <span class="brand-name">Renwick Tolliver<br>Construction</span>
  </div>
  <p class="front-web">www.renwick-tolliver.co.uk</p>
</section>

<section class="card card-back" aria-label="Card back">
  <div class="brand">
    <span class="brand-mark"></span>
    <span class="brand-name">Renwick Tolliver<br>Construction</span>
  </div>

  <div class="person">
    <p class="person-name">Lionel Ashby</p>
    <p class="person-role">Managing Director</p>
  </div>

  <div class="divider"></div>

  <ul class="contacts">
    <li>
      <svg viewBox="0 0 24 24" aria-hidden="true"><path d="M6.6 10.8a15.1 15.1 0 0 0 6.6 6.6l2.2-2.2c.3-.3.7-.4 1-.2 1.1.4 2.3.6 3.6.6.6 0 1 .4 1 1V20c0 .6-.4 1-1 1A17 17 0 0 1 3 4c0-.6.4-1 1-1h3.5c.6 0 1 .4 1 1 0 1.3.2 2.5.6 3.6.1.3 0 .7-.2 1z"/></svg>
      07822254961
    </li>
    <li>
      <svg viewBox="0 0 24 24" aria-hidden="true"><path d="M2 5h20v14H2z M3 6l9 7 9-7" /></svg>
      info@renwick-tolliver
    </li>
    <li>
      <svg viewBox="0 0 24 24" aria-hidden="true"><circle cx="12" cy="12" r="10"/></svg>
      www.renwick-tolliver.co.uk
    </li>
  </ul>
</section>

</body>
</html>
```